Northfield Builders Guild Business card

We are looking for a new business card design with photo included.
Our business is a nonprofit construction contractor membership organization. We offer business education, assist with business setup and licensing, provide safety training, and provide a member directory.
URL: www.builderslinkguild.org
Color code:
CMYK: 0 cyan, 42 magenta, 100 yellow, 0 black for Print.
Hexidecimal: #FF9900
RGB: R 255; G 153; B 0

```html
<!DOCTYPE html>
<html lang="en">
<head>
<meta charset="utf-8">
<title>Northfield Builders Guild – Business Card</title>
<link rel="stylesheet" href="https://fonts.googleapis.com/css2?family=Jost:wght@400;700&family=Oswald:wght@500&display=swap">
<style>
  :root {
    --backdrop: #9a9a9a;
    --card: #333132;
    --accent: #ff9900;
    --text-light: #f2f2f2;
    --logo-grey: #8e8c8d;
    --divider: #5a5858;
  }
  * { box-sizing: border-box; margin: 0; padding: 0; }
  html, body { width: 1200px; height: 800px; overflow: hidden; }
  body {
    background: var(--backdrop);
    display: flex;
    align-items: center;
    justify-content: center;
    gap: 50px;
    font-family: "Jost", sans-serif;
  }
  .card {
    width: 540px;
    height: 309px;
    background: var(--card);
    border-bottom: 3px solid var(--accent);
    box-shadow: 0 12px 28px rgba(0,0,0,0.35);
    position: relative;
  }
  /* Contact side */
  .card--contact {
    display: flex;
    align-items: center;
    justify-content: center;
    gap: 26px;
  }
  .identity { text-align: right; }
  .identity__name {
    font-family: "Oswald", sans-serif;
    font-weight: 500;
    font-size: 28px;
    letter-spacing: 0.5px;
    color: var(--accent);
    line-height: 1;
  }
  .identity__title {
    font-size: 15px;
    color: var(--text-light);
    margin-top: 4px;
  }
  .divider {
    width: 1px;
    height: 112px;
    background: var(--divider);
  }
  .contact { color: var(--text-light); font-size: 12.5px; line-height: 1.4; }
  .contact__address { margin-bottom: 8px; }
  .contact__list { list-style: none; }
  .contact__item { display: flex; align-items: center; gap: 8px; }
  .contact__icon { width: 11px; height: 11px; flex: none; }
  /* Brand side */
  .card--brand {
    display: flex;
    align-items: center;
    justify-content: center;
  }
  .brand-name {
    font-family: "Jost", sans-serif;
    font-weight: 700;
    font-size: 38px;
    line-height: 1.05;
    text-transform: uppercase;
    color: var(--logo-grey);
    text-align: center;
    letter-spacing: 1px;
  }
</style>
</head>
<body>
  <section class="card card--contact">
    <div class="identity">
      <p class="identity__name">DANIEL REYES</p>
      <p class="identity__title">President</p>
    </div>
    <div class="divider"></div>
    <div class="contact">
      <p class="contact__address">4820 Cedar Hollow Rd.,<br>Suite #210, Northfield, OR 97388</p>
      <ul class="contact__list">
        <li class="contact__item">
          <svg class="contact__icon" viewBox="0 0 12 12"><path d="M2.5 1 L4.5 1 L5.3 3.6 L4 4.6 Q5.2 7 7.4 8 L8.4 6.7 L11 7.5 L11 9.5 Q10.5 11 9 11 Q1 10 1 2.5 Q1 1.2 2.5 1 Z" fill="var(--accent)"/></svg>
          (555) 318-2740
        </li>
        <li class="contact__item">
          <svg class="contact__icon" viewBox="0 0 12 12"><rect x="3" y="0.8" width="6" height="10.4" rx="1" fill="none" stroke="var(--accent)" stroke-width="1.3"/></svg>
          555.204.6613
        </li>
        <li class="contact__item">
          <svg class="contact__icon" viewBox="0 0 12 12"><rect x="0.5" y="2" width="11" height="8" fill="var(--accent)"/><path d="M0.5 2 L6 6.5 L11.5 2" fill="none" stroke="var(--card)" stroke-width="1"/></svg>
          help@nbguild.org
        </li>
        <li class="contact__item">
          <svg class="contact__icon" viewBox="0 0 12 12"><circle cx="6" cy="6" r="5.5" fill="var(--accent)"/><path d="M0.5 6 H11.5 M6 0.5 Q3 6 6 11.5 M6 0.5 Q9 6 6 11.5" fill="none" stroke="var(--card)" stroke-width="0.8"/></svg>
          www.builderslinkguild.org
        </li>
      </ul>
    </div>
  </section>

  <section class="card card--brand">
    <p class="brand-name">Northfield<br>Builders Guild</p>
  </section>
</body>
</html>
```